Global Beard Oil Review Business needs a refresh

topwhiskertonic.net is a global business who's mission is to curate all available beard oils from around the world, review and grade them and present this curated collection to the user of the website.

The scope of this job includes the web site design and the design of a suitable logo to be used in the site header.

The existing site can be seen on http://topwhiskertonic.net, however this is a mock-up only the style and logo should NOT be used. This is to give you an idea of the concept of the site only.

This job is for PSD design only.

See attached design brief for detailed design requirements.
Updates

Project Deadline Extended
Reason: Extending deadline by 5 days to allow for final submissions

Target Market(s)

Men's grooming / retail

Industry/Entity Type

Retail

Number of Pages Required

2 page

Font styles to use
Sans Serif

Requirements
Must have
• 1) Comparison Table
• 2) Side Bar
• 3) Header area
• 4) Photo of Delvin Marsk (attached - can be circular or "cut-out")
• 5) Cool beard-oriented custom design background (e.g., stylistic black/brown on brown/orange beard background. I envision this beard background "drawing" rather than photo based)
• (see attached design requirements for details)
Nice to have
• Signature style writing at top with name "Delvin Marsk"
Should not have
• Do NOT use the look & feel or logo from the existing site.

```html
<!DOCTYPE html>
<html lang="en">
<head>
<meta charset="utf-8">
<title>Top Whisker Tonic – Beard Oil Reviews</title>
<link rel="stylesheet" href="https://fonts.googleapis.com/css2?family=Amatic+SC:wght@700&family=Raleway:wght@400;600;700&family=Mr+Dafoe&display=swap">
<style>
:root{
  --orange:#f7a800;
  --orange-dark:#e59a00;
  --maroon:#5c0c0c;
  --maroon-text:#6b1414;
  --ink:#222222;
  --muted:#666666;
  --line:#e3e3e3;
  --panel:#ffffff;
  --nav-bg:#ececec;
  --hero-bg:#121212;
  --pattern-a:#e9e9e9;
  --pattern-b:#cfcfcf;
  --btn-grey:#c9c9c9;
}
*{box-sizing:border-box;margin:0;padding:0}
html,body{width:1200px;height:2557px;overflow:hidden}
body{position:relative;font-family:'Raleway',Arial,sans-serif;color:var(--ink);
  background:linear-gradient(135deg,var(--pattern-a),var(--pattern-b) 50%,var(--pattern-a));}
.backdrop{position:absolute;inset:0}
.display{font-family:'Amatic SC','Arial Narrow',sans-serif;font-weight:700}

/* header */
.site-header{position:absolute;left:0;top:0;width:1200px;height:136px}
.brand{position:absolute;left:77px;top:30px;width:230px;display:flex;align-items:center;gap:12px}
.brand-dot{flex:0 0 34px;height:34px;border-radius:50%;background:var(--orange)}
.brand-name{font-family:'Amatic SC','Arial Narrow',sans-serif;font-weight:700;font-size:38px;line-height:36px;color:var(--orange)}
.founder-photo{position:absolute;left:324px;top:0;width:160px;height:160px;border-radius:50%;border:6px solid #fff;
  background:radial-gradient(circle at 50% 40%,#8a8a8a,#3a3a3a 70%);box-shadow:0 2px 6px rgba(0,0,0,.35);z-index:3}
.signature{position:absolute;left:486px;top:22px;font-family:'Mr Dafoe',cursive;font-size:32px;color:#333;transform:rotate(-6deg);white-space:nowrap}
.contact{position:absolute;left:736px;top:24px;display:flex;align-items:center;gap:12px;font-size:17px;color:#333}
.icon-circle{width:36px;height:36px;border-radius:50%;background:var(--orange);display:flex;align-items:center;justify-content:center}
.socials{position:absolute;display:flex;gap:10px}
.socials span{width:27px;height:27px;border-radius:50%;background:var(--orange);display:block}
.site-header .socials{left:984px;top:31px}
.main-nav{position:absolute;left:520px;top:85px;width:614px;height:38px;background:var(--nav-bg);display:flex;align-items:center;padding-left:10px;font-size:16px}
.main-nav a{color:#333;text-decoration:none;padding:4px 12px}
.main-nav a.active{background:var(--maroon);color:#fff}
.main-nav .sep{width:4px;height:4px;border-radius:50%;background:#555}

/* page panel */
.page{position:absolute;left:58px;top:136px;width:1084px;height:2378px;background:var(--panel)}
.hero{position:absolute;left:8px;top:0;width:1068px;height:410px;background:var(--hero-bg);overflow:hidden}
.hero-photo{position:absolute;left:60px;top:0;width:360px;height:410px;background:linear-gradient(90deg,#1c1c1c,#5a5048 45%,#2a2622 80%,#121212)}
.hero-title{position:absolute;left:551px;top:80px;font-size:70px;line-height:92px;color:#fff;white-space:nowrap}
.btn{display:inline-block;background:var(--orange);color:#222;text-decoration:none;text-align:center;font-family:'Raleway',Arial,sans-serif}
.hero .btn{position:absolute;left:551px;top:270px;width:143px;height:54px;line-height:54px;font-size:22px}
.hero-dots{position:absolute;left:555px;top:340px;display:flex;gap:9px}
.hero-dots span{width:8px;height:8px;border-radius:50%;background:#fff}
.hero-dots span.on{background:var(--orange)}

.welcome{position:absolute;left:0;top:440px;width:1084px;text-align:center}
.welcome h1{font-size:64px;color:#222;line-height:1}
.welcome h1 em{font-style:normal;color:var(--maroon)}
.welcome p{width:886px;margin:22px auto 0;font-size:13.5px;line-height:21px;color:#333}

.process{position:absolute;left:0;top:640px;width:1084px;height:180px}
.step{position:absolute;width:200px;text-align:center}
.step .disc{width:110px;height:110px;border-radius:50%;background:var(--orange);margin:0 auto;display:flex;align-items:center;justify-content:center}
.step h3{font-size:30px;margin-top:14px;color:#222}

/* table */
.compare{position:absolute;left:22px;top:851px;width:781px;border-collapse:collapse;table-layout:fixed;font-size:13px}
.compare th{height:61px;font-size:13px;font-weight:700;padding:0 4px}
.compare th.key{background:var(--maroon);color:var(--orange)}
.compare th.score{background:var(--orange);color:var(--maroon)}
.compare td{height:91.5px;border:1px solid var(--line);vertical-align:top;padding-top:26px;text-align:center;color:#333}
.compare td.product{text-align:left;padding:14px 6px 0 10px}
.product-cell{display:flex;gap:10px}
.thumb{flex:0 0 44px;height:48px;background:linear-gradient(160deg,#f1d9a0,#d9a23a)}
.thumb.bottle{background:linear-gradient(160deg,#e8dcd0,#7a3e1e)}
.product-name{font-weight:700;font-size:15px;color:var(--maroon-text);line-height:19px}
.supplier{font-size:12px;color:#444}
.compare .btn{width:70px;height:25px;line-height:25px;font-size:12px;color:#fff;margin-top:-2px}
.load-more{position:absolute;left:336px;top:2307px;width:152px;height:33px;background:var(--btn-grey);color:#fff;font-size:14px;text-align:center;line-height:33px}

/* sidebar */
.subscribe{position:absolute;left:827px;top:851px;width:235px;height:343px;background:var(--orange);text-align:center;padding:14px 16px}
.subscribe h2{font-size:36px;line-height:40px;color:var(--maroon)}
.subscribe p{font-size:12.5px;line-height:19px;margin-top:18px;color:#222}
.subscribe .field{background:#fff;height:36px;margin-top:14px;font-size:12px;color:#999;line-height:36px}
.subscribe .signup{background:var(--maroon);color:#fff;height:36px;line-height:36px;font-weight:700;font-size:14px;margin-top:14px}
.subscribe small{display:block;font-size:10.5px;line-height:15px;color:#7a4a00;margin-top:16px}
.sidebar-title{position:absolute;left:827px;top:1240px;font-size:42px;color:var(--maroon)}
.post{position:absolute;left:827px;width:235px}
.post .cover{height:155px}
.post h4{font-size:15px;font-weight:700;color:var(--orange);margin-top:16px}
.post time{display:block;font-size:13px;color:#333;margin-top:10px}

/* footer */
.site-footer{position:absolute;left:0;top:2518px;width:1200px;height:39px;background:var(--orange);color:#fff;font-size:13px}
.site-footer p{position:absolute;left:80px;top:11px}
.site-footer .socials{left:982px;top:6px}
.site-footer .socials span{background:transparent;border:2px solid #fff}
</style>
</head>
<body>
<div class="backdrop" role="img" aria-label="Light grey background pattern of drawn bearded faces"></div>

<header class="site-header">
  <div class="brand"><span class="brand-dot"></span><span class="brand-name">Top Whisker<br>Tonic</span></div>
  <div class="founder-photo" role="img" aria-label="Circular portrait photo of founder Delvin Marsk"></div>
  <div class="signature">Delvin Marsk</div>
  <div class="contact">
    <span class="icon-circle">
      <svg width="18" height="18" viewBox="0 0 24 24"><path d="M6.6 10.8c1.4 2.8 3.8 5.1 6.6 6.6l2.2-2.2c.3-.3.7-.4 1-.2 1.1.4 2.3.6 3.6.6.6 0 1 .4 1 1V20c0 .6-.4 1-1 1C10.6 21 3 13.4 3 4c0-.6.4-1 1-1h3.5c.6 0 1 .4 1 1 0 1.3.2 2.5.6 3.6.1.3 0 .7-.2 1L6.6 10.8z" fill="#5c0c0c"/></svg>
    </span>
    <span>info@topwhiskertonic.net</span>
  </div>
  <div class="socials"><span></span><span></span><span></span><span></span></div>
  <nav class="main-nav">
    <a class="active" href="#">Home</a>
    <a href="#">About</a><span class="sep"></span>
    <a href="#">Our Charter</a><span class="sep"></span>
    <a href="#">Beard Oil Review Methodology</a><span class="sep"></span>
    <a href="#">Blog</a>
  </nav>
</header>

<main class="page">
  <section class="hero">
    <div class="hero-photo" role="img" aria-label="Photo of a tattooed bearded man in a white t-shirt"></div>
    <h2 class="hero-title display">Curate, Review &amp; Grade<br>Then Present</h2>
    <a class="btn" href="#">See Table</a>
    <div class="hero-dots"><span></span><span></span><span></span><span class="on"></span></div>
  </section>

  <section class="welcome">
    <h1 class="display">Welcome To <em>Top Whisker Tonic</em></h1>
    <p>We are a global business with the mission to curate all available beard oils from around the world, review &amp; grade them &amp; present this curated collection to the users of the site. Our Target Audience are all grooming men. Lorem ipsum dolor sit amet, consectetuer adipiscing elit, sed diam nonummy nibh euismod tincidunt ut laoreet dolore magna aliquam erat volutpat. Lorem ipsum dolor sit amet, consectetuer adipiscing elit, sed diam nonummy nibh euismod tincidunt ut laoreet dolore magna aliquam erat volutpat.</p>
  </section>

  <section class="process">
    <svg width="1084" height="180" style="position:absolute;left:0;top:0">
      <path id="arcOne" d="M230 78 Q 390 150 540 110" fill="none" stroke="#6b1414" stroke-width="1.2" stroke-dasharray="2 3"/>
      <path id="arcTwo" d="M606 50 Q 760 -10 915 70" fill="none" stroke="#6b1414" stroke-width="1.2" stroke-dasharray="2 3"/>
      <path d="M533 104 l8 5 -9 3" fill="none" stroke="#6b1414" stroke-width="1.2"/>
      <path d="M907 62 l8 8 -10 0" fill="none" stroke="#6b1414" stroke-width="1.2"/>
      <text font-family="Raleway, sans-serif" font-size="13" fill="#6b1414" dy="-6"><textPath href="#arcOne" startOffset="10%">We curate all available beard oils</textPath></text>
      <text font-family="Raleway, sans-serif" font-size="13" fill="#6b1414" dy="-6"><textPath href="#arcTwo" startOffset="14%">Review &amp; Grade them &amp; Present</textPath></text>
    </svg>
    <div class="step" style="left:67px;top:0">
      <div class="disc"><svg width="50" height="50" viewBox="0 0 24 24"><path d="M4 12l5 5L20 6" fill="none" stroke="#5c0c0c" stroke-width="3"/></svg></div>
      <h3 class="display">Curate</h3>
    </div>
    <div class="step" style="left:442px;top:0">
      <div class="disc"><svg width="50" height="50" viewBox="0 0 24 24"><path d="M12 2l3 6.5 7 .8-5.2 4.8 1.4 7L12 17.6 5.8 21.1l1.4-7L2 9.3l7-.8z" fill="#5c0c0c"/></svg></div>
      <h3 class="display">Review &amp; Grade</h3>
    </div>
    <div class="step" style="left:815px;top:0">
      <div class="disc"><svg width="50" height="50" viewBox="0 0 24 24"><rect x="3" y="4" width="18" height="14" fill="none" stroke="#5c0c0c" stroke-width="2"/><path d="M3 8h18M12 20v-8M8.5 15.5L12 12l3.5 3.5" fill="none" stroke="#5c0c0c" stroke-width="2"/></svg></div>
      <h3 class="display">Present</h3>
    </div>
  </section>

  <table class="compare">
    <colgroup><col style="width:191px"><col style="width:72px"><col style="width:90px"><col style="width:101px"><col style="width:61px"><col style="width:61px"><col style="width:55px"><col style="width:58px"><col style="width:92px"></colgroup>
    <thead><tr>
      <th class="key">Product, Supplier</th><th class="key">Origin ▾</th><th class="key">Base Oil ▾</th><th class="key">Scent ▾</th>
      <th class="score">Aroma ▾</th><th class="score">Thera. ▾<br>Affect</th><th class="score">Value ▾</th><th class="score">Over ▾<br>All</th><th class="score">Get It</th>
    </tr></thead>
    <tbody>
      <tr><td class="product"><div class="product-cell"><div class="thumb" role="img" aria-label="Product box photo"></div><div><div class="product-name">Trail Grooming</div><div class="supplier">-Rugged Fellow</div></div></div></td><td>USA</td><td>Jojoba,<br>Hempseed</td><td>Spice Market</td><td>5</td><td>5</td><td>5</td><td>5</td><td><a class="btn" href="#">Buy Now</a></td></tr>
      <tr><td class="product"><div class="product-cell"><div class="thumb bottle" role="img" aria-label="Bottle photo"></div><div><div class="product-name">Harbor Cedar Tobacco</div><div class="supplier">-Rugged Fellow</div></div></div></td><td>USA</td><td>Jojoba,<br>Hempseed</td><td>Spice Market</td><td>5</td><td>5</td><td>5</td><td>5</td><td><a class="btn" href="#">Buy Now</a></td></tr>
      <tr><td class="product"><div class="product-cell"><div class="thumb" role="img" aria-label="Product box photo"></div><div><div class="product-name">Trail Grooming</div><div class="supplier">-Rugged Fellow</div></div></div></td><td>USA</td><td>Jojoba,<br>Hempseed</td><td>Spice Market</td><td>5</td><td>5</td><td>5</td><td>5</td><td><a class="btn" href="#">Buy Now</a></td></tr>
      <tr><td class="product"><div class="product-cell"><div class="thumb bottle" role="img" aria-label="Bottle photo"></div><div><div class="product-name">Harbor Cedar Tobacco</div><div class="supplier">-Rugged Fellow</div></div></div></td><td>USA</td><td>Jojoba,<br>Hempseed</td><td>Spice Market</td><td>5</td><td>5</td><td>5</td><td>5</td><td><a class="btn" href="#">Buy Now</a></td></tr>
      <tr><td class="product"><div class="product-cell"><div class="thumb" role="img" aria-label="Product box photo"></div><div><div class="product-name">Trail Grooming</div><div class="supplier">-Rugged Fellow</div></div></div></td><td>USA</td><td>Jojoba,<br>Hempseed</td><td>Spice Market</td><td>5</td><td>5</td><td>5</td><td>5</td><td><a class="btn" href="#">Buy Now</a></td></tr>
      <tr><td class="product"><div class="product-cell"><div class="thumb bottle" role="img" aria-label="Bottle photo"></div><div><div class="product-name">Harbor Cedar Tobacco</div><div class="supplier">-Rugged Fellow</div></div></div></td><td>USA</td><td>Jojoba,<br>Hempseed</td><td>Spice Market</td><td>5</td><td>5</td><td>5</td><td>5</td><td><a class="btn" href="#">Buy Now</a></td></tr>
      <tr><td class="product"><div class="product-cell"><div class="thumb" role="img" aria-label="Product box photo"></div><div><div class="product-name">Trail Grooming</div><div class="supplier">-Rugged Fellow</div></div></div></td><td>USA</td><td>Jojoba,<br>Hempseed</td><td>Spice Market</td><td>5</td><td>5</td><td>5</td><td>5</td><td><a class="btn" href="#">Buy Now</a></td></tr>
      <tr><td class="product"><div class="product-cell"><div class="thumb bottle" role="img" aria-label="Bottle photo"></div><div><div class="product-name">Harbor Cedar Tobacco</div><div class="supplier">-Rugged Fellow</div></div></div></td><td>USA</td><td>Jojoba,<br>Hempseed</td><td>Spice Market</td><td>5</td><td>5</td><td>5</td><td>5</td><td><a class="btn" href="#">Buy Now</a></td></tr>
      <tr><td class="product"><div class="product-cell"><div class="thumb" role="img" aria-label="Product box photo"></div><div><div class="product-name">Trail Grooming</div><div class="supplier">-Rugged Fellow</div></div></div></td><td>USA</td><td>Jojoba,<br>Hempseed</td><td>Spice Market</td><td>5</td><td>5</td><td>5</td><td>5</td><td><a class="btn" href="#">Buy Now</a></td></tr>
      <tr><td class="product"><div class="product-cell"><div class="thumb bottle" role="img" aria-label="Bottle photo"></div><div><div class="product-name">Harbor Cedar Tobacco</div><div class="supplier">-Rugged Fellow</div></div></div></td><td>USA</td><td>Jojoba,<br>Hempseed</td><td>Spice Market</td><td>5</td><td>5</td><td>5</td><td>5</td><td><a class="btn" href="#">Buy Now</a></td></tr>
      <tr><td class="product"><div class="product-cell"><div class="thumb" role="img" aria-label="Product box photo"></div><div><div class="product-name">Trail Grooming</div><div class="supplier">-Rugged Fellow</div></div></div></td><td>USA</td><td>Jojoba,<br>Hempseed</td><td>Spice Market</td><td>5</td><td>5</td><td>5</td><td>5</td><td><a class="btn" href="#">Buy Now</a></td></tr>
      <tr><td class="product"><div class="product-cell"><div class="thumb bottle" role="img" aria-label="Bottle photo"></div><div><div class="product-name">Harbor Cedar Tobacco</div><div class="supplier">-Rugged Fellow</div></div></div></td><td>USA</td><td>Jojoba,<br>Hempseed</td><td>Spice Market</td><td>5</td><td>5</td><td>5</td><td>5</td><td><a class="btn" href="#">Buy Now</a></td></tr>
      <tr><td class="product"><div class="product-cell"><div class="thumb" role="img" aria-label="Product box photo"></div><div><div class="product-name">Trail Grooming</div><div class="supplier">-Rugged Fellow</div></div></div></td><td>USA</td><td>Jojoba,<br>Hempseed</td><td>Spice Market</td><td>5</td><td>5</td><td>5</td><td>5</td><td><a class="btn" href="#">Buy Now</a></td></tr>
      <tr><td class="product"><div class="product-cell"><div class="thumb bottle" role="img" aria-label="Bottle photo"></div><div><div class="product-name">Harbor Cedar Tobacco</div><div class="supplier">-Rugged Fellow</div></div></div></td><td>USA</td><td>Jojoba,<br>Hempseed</td><td>Spice Market</td><td>5</td><td>5</td><td>5</td><td>5</td><td><a class="btn" href="#">Buy Now</a></td></tr>
      <tr><td class="product"><div class="product-cell"><div class="thumb" role="img" aria-label="Product box photo"></div><div><div class="product-name">Trail Grooming</div><div class="supplier">-Rugged Fellow</div></div></div></td><td>USA</td><td>Jojoba,<br>Hempseed</td><td>Spice Market</td><td>5</td><td>5</td><td>5</td><td>5</td><td><a class="btn" href="#">Buy Now</a></td></tr>
    </tbody>
  </table>
  <div class="load-more">Loading More...</div>

  <aside>
    <div class="subscribe">
      <h2 class="display">Get More Stuff Like This In Your InBox</h2>
      <p>Subscribe to our mailing list &amp; get interesting stuff &amp; updates.</p>
      <div class="field">Enter your email here</div>
      <div class="signup">SIGNUP NOW</div>
      <small>We respect your privacy and take protecting it seriously</small>
    </div>
    <h2 class="sidebar-title display">Latest Blog</h2>
    <article class="post" style="top:1317px">
      <div class="cover" role="img" aria-label="Blog cover photo of a bearded man with a beard oil title" style="background:linear-gradient(120deg,#2e3438,#8a9299 60%,#d8d8d8)"></div>
      <h4>How to Use Marlo's Beard Oil</h4><time>February 12, 2016</time>
    </article>
    <article class="post" style="top:1576px">
      <div class="cover" role="img" aria-label="Photo of herbs and oil bottles on a table" style="background:linear-gradient(120deg,#b98b45,#6f6a3a 50%,#c9b27a)"></div>
      <h4>How to Use Marlo's Beard Oil</h4><time>February 12, 2016</time>
    </article>
    <article class="post" style="top:1825px">
      <div class="cover" role="img" aria-label="Photo of a bearded man with a pipe in sunlight" style="background:linear-gradient(120deg,#f4e2b0,#a9864e 50%,#4a4a3a)"></div>
      <h4>How to Use Marlo's Beard Oil</h4><time>February 12, 2016</time>
    </article>
    <article class="post" style="top:2075px">
      <div class="cover" role="img" aria-label="Photo of a man trimming his beard" style="background:linear-gradient(120deg,#dfe5e8,#9fb0ba 55%,#c9d3d8)"></div>
      <h4>How to Use Marlo's Beard Oil</h4><time>February 12, 2016</time>
    </article>
  </aside>
</main>

<footer class="site-footer">
  <p>Copyright 2016 Top Whisker Tonic. All Rights Reserved.</p>
  <div class="socials"><span></span><span></span><span></span><span></span></div>
</footer>
</body>
</html>
```